New Dental Office Needs an Attractive and user friendly Website Designed

I need a website for a new dental office. The Name is Harrowfield Dentistry. I would like a Modern design with a user friendly interface and usability.
I would like a landing page, a page that lists the services we offer: Cosmetic Dentistry, Implants, Dental Hygiene, Emergency Services, Restorations, Dentures
Target Market(s)
Mid to upper class
Industry/Entity Type
Dentistry
Coding
Number of Pages Required
1 page
Requirements
Must have
- Landing page that has a scheduling option, Procedures, operating hours, and contact us info
Nice to have
- Appealing design, Soft comforting colors. Easy to navigate page, Modern and professional.

```html
<!DOCTYPE html>
<html lang="en">
<head>
<meta charset="utf-8">
<title>Harrowfield Dentistry</title>
<link rel="stylesheet" href="https://fonts.googleapis.com/css2?family=Libre+Baskerville:wght@400;700&family=Poppins:ital,wght@0,400;0,500;0,600;0,700;1,400&display=swap">
<style>
:root{
  --teal:#2bbcb0;
  --blue:#2f86ee;
  --brand:#2a7fd6;
  --ink:#1c1c1c;
  --text:#3a3a3a;
  --muted:#707070;
  --hero-bg:#f1f4fa;
  --line:#dcdcdc;
  --grad:linear-gradient(90deg,var(--teal),var(--blue));
  --photo-a:#c9d9e6;
  --photo-b:#e8eef3;
}
*{margin:0;padding:0;box-sizing:border-box}
html,body{width:1200px;height:5106px;overflow:hidden}
body{position:relative;background:#fff;font-family:"Poppins",sans-serif;color:var(--text)}
.abs{position:absolute}
.serif{font-family:"Libre Baskerville",serif}
.btn{position:absolute;display:flex;align-items:center;justify-content:center;background:var(--grad);color:#fff;border-radius:5px;font-weight:500}
.photo{position:absolute;background:linear-gradient(135deg,var(--photo-a),var(--photo-b))}

/* header */
.site-header{position:absolute;left:0;top:0;width:1200px;height:130px;background:#fff}
.logo{position:absolute;text-align:center;font-family:"Libre Baskerville",serif;color:var(--ink)}
.logo .name{display:block;line-height:1}
.logo .sub{display:block;letter-spacing:.3em;font-family:"Poppins",sans-serif;font-weight:600}
.nav{position:absolute;top:60px;font-size:13px;color:var(--ink)}
.nav.active{color:var(--brand)}
.call-box{position:absolute;left:885px;top:0;width:315px;height:128px}
.call-label{position:absolute;left:1018px;top:22px;font-size:11px;font-weight:700;color:#fff}
.call-phone{position:absolute;left:968px;top:66px;font-size:24px;font-weight:500;color:#fff}

/* hero */
.hero{position:absolute;left:0;top:130px;width:1200px;height:598px;background:var(--hero-bg);overflow:hidden}
.hero-welcome{position:absolute;left:102px;top:168px;font-size:21px;color:var(--ink)}
.hero-title{position:absolute;left:100px;top:192px;font-size:76px;color:var(--brand);font-family:"Libre Baskerville",serif}
.hero-text{position:absolute;left:102px;top:304px;width:540px;font-size:15.5px;line-height:29px;color:var(--ink)}

/* stats */
.stats{position:absolute;left:0;top:728px;width:1200px;height:310px;background:var(--grad)}
.stat{position:absolute;top:52px;width:240px;margin-left:-120px;text-align:center}
.stat-ring{width:142px;height:142px;margin:0 auto;border-radius:50%;background:#fff;display:flex;align-items:center;justify-content:center}
.stat-ring span{width:120px;height:120px;border-radius:50%;border:2px dotted var(--brand);display:flex;align-items:center;justify-content:center;font-size:40px;font-weight:600;color:#1c6b8a}
.stat-label{margin-top:24px;font-family:"Libre Baskerville",serif;font-weight:700;font-size:17px;color:#fff}

/* section headings */
.sec-title{position:absolute;font-family:"Libre Baskerville",serif;font-variant:small-caps;font-size:36px;color:var(--brand);line-height:1}
.sec-sub{position:absolute;font-size:13px;font-weight:600;color:var(--ink);display:flex;align-items:center;gap:8px}
.sec-sub i{display:block;width:30px;height:2px;background:var(--ink)}

/* about */
.about-lead{position:absolute;left:132px;top:1196px;width:440px;font-size:20px;line-height:29px;color:var(--ink);font-weight:500}
.about-body{position:absolute;left:132px;top:1257px;width:428px;font-size:13.2px;line-height:26.7px;color:var(--muted);text-align:justify}
.ring-photo{position:absolute;border-radius:50%;border:3px solid var(--teal)}
.ring-photo .photo{border-radius:50%}

/* services */
.card{position:absolute;width:331px;height:410px;background:#fff;box-shadow:0 2px 12px rgba(0,0,0,.15)}
.card .photo{left:17px;top:17px;width:297px;height:215px}
.card h3{position:absolute;left:0;top:254px;width:100%;text-align:center;font-size:21px;font-weight:500;color:var(--brand)}
.card p{position:absolute;left:22px;top:297px;width:287px;text-align:center;font-size:13px;line-height:25.5px;color:var(--text)}
.card .btn{left:110px;top:392px;width:111px;height:34px;font-size:11px;font-weight:600}

/* banner */
.banner{position:absolute;left:0;top:2776px;width:1200px;height:449px;background:linear-gradient(90deg,#e8ebef,#eef0f3 50%,#e6e9ee)}
.banner h2{position:absolute;left:0;top:114px;width:1200px;text-align:center;font-family:"Libre Baskerville",serif;font-weight:700;font-size:40px;line-height:46px;color:#111}
.banner p{position:absolute;left:300px;top:222px;width:600px;text-align:center;font-size:13.5px;line-height:24px;color:var(--ink)}

/* testimonials */
.quote-card{position:absolute;width:466px;height:208px;border:1.5px solid var(--line);border-radius:24px;background:#fff}
.quote-card h4{position:absolute;left:36px;top:42px;font-size:13px;font-weight:600;color:var(--ink)}
.quote-card .stars{position:absolute;right:34px;top:40px;font-size:15px;color:#f3b21c;letter-spacing:-1px}
.quote-card p{position:absolute;left:36px;top:72px;width:396px;font-size:11px;line-height:22px;font-style:italic;color:var(--text)}
.avatar{position:absolute;width:68px;height:68px;border-radius:50%;background:linear-gradient(135deg,#c7ccd2,#eceef0);border:3px solid #fff;box-shadow:0 0 0 1px var(--line)}
.person{position:absolute;font-size:13px;font-weight:600;color:var(--brand);line-height:16px}
.person small{display:block;font-size:11px;font-weight:400;color:var(--ink)}
.dot{position:absolute;top:3891px;width:13px;height:13px;border-radius:50%;border:1.5px solid #999}

/* contact */
.field{position:absolute;height:50px;border:1px solid #e2e2e2;background:#fff;font-size:12px;color:#bdbdbd;padding:17px 10px}

/* footer */
.footer{position:absolute;left:0;top:4610px;width:1200px;height:496px;background:linear-gradient(100deg,#2fb9b3 0%,#2fa3d8 45%,#3087ee 100%);color:#fff}
.f-head{position:absolute;top:124px;font-family:"Libre Baskerville",serif;font-size:20px;color:#fff}
.f-item{position:absolute;font-size:14px;color:#fff}
.f-item::before{content:"";position:absolute;left:-18px;top:7px;width:7px;height:7px;border-radius:50%;background:var(--teal)}
.f-icon{position:absolute;width:34px;height:34px;border-radius:50%;background:var(--teal);display:flex;align-items:center;justify-content:center}
.f-text{position:absolute;font-size:14px;line-height:25px;color:#fff}
.social{position:absolute;top:4872px;width:26px;height:26px;border-radius:50%;background:var(--teal)}
.copyright{position:absolute;left:0;top:5052px;width:1200px;text-align:center;font-size:13px;color:#fff}
</style>
</head>
<body>

<!-- Header -->
<header class="site-header">
  <div class="logo" style="left:66px;top:22px;width:252px">
    <span class="name" style="font-size:44px">Harrowfield</span>
    <span class="sub" style="font-size:17px;margin-top:6px">— DENTISTRY —</span>
  </div>
  <span class="nav active" style="left:441px">Home</span>
  <span class="nav" style="left:508px">About Us</span>
  <span class="nav" style="left:593px">Services</span>
  <span class="nav" style="left:676px">Testimonials</span>
  <span class="nav" style="left:791px">Contact Us</span>
  <svg class="call-box" viewBox="0 0 315 128" aria-hidden="true"><polygon points="0,0 315,0 315,128 60,128" fill="var(--teal)"/></svg>
  <svg class="abs" style="left:972px;top:14px" width="36" height="36" viewBox="0 0 36 36" aria-hidden="true"><circle cx="18" cy="18" r="16" fill="none" stroke="#fff" stroke-width="1.5"/><path d="M12 11c1-1 2-1 3 0l2 3c.5 1 0 2-1 2.5 1 2 2.5 3.5 4.5 4.5.5-1 1.5-1.5 2.5-1l3 2c1 1 1 2 0 3-2 2-5 1.5-8-1s-6-6-7-8.5c-1-2-.5-3.5 1-4.5z" fill="#fff"/></svg>
  <span class="call-label">CALL US TODAY!</span>
  <span class="call-phone">(412) 555-0148</span>
</header>

<!-- Hero -->
<section class="hero">
  <span class="hero-welcome">Welcome To</span>
  <h1 class="hero-title" style="font-weight:400">Harrowfield</h1>
  <p class="hero-text">Lorem ipsum dolor sit amet, consectetur adipiscing elit, sed do eiusmod tempor incididunt ut labore et dolore magna aliqua.</p>
  <span class="btn" style="left:102px;top:378px;width:146px;height:44px;font-size:15px;font-weight:400">Know More</span>
  <svg class="abs" style="left:500px;top:0" width="700" height="598" viewBox="0 0 700 598" role="img" aria-label="Photo of a dentist treating a smiling female patient in the dental chair">
    <defs><linearGradient id="heroPhoto" x1="0" y1="0" x2="1" y2="1"><stop offset="0" stop-color="#e7edf3"/><stop offset=".55" stop-color="#c8d3e0"/><stop offset="1" stop-color="#b3a9cf"/></linearGradient></defs>
    <polygon points="20,0 700,0 700,598 300,598" fill="url(#heroPhoto)"/>
    <polygon points="8,0 40,0 132,170 100,170" fill="var(--teal)"/>
    <polygon points="555,25 570,18 650,200 632,208" fill="var(--teal)"/>
    <polygon points="570,40 590,30 700,280 700,320" fill="var(--blue)"/>
    <polygon points="210,440 228,430 300,580 282,588" fill="var(--blue)"/>
    <polygon points="255,480 270,472 340,598 320,598" fill="var(--teal)"/>
  </svg>
</section>

<!-- Stats -->
<section class="stats">
  <div class="stat" style="left:190px"><div class="stat-ring"><span>6K+</span></div><div class="stat-label">Implants Placed</div></div>
  <div class="stat" style="left:451px"><div class="stat-ring"><span>10K+</span></div><div class="stat-label">Smiles Transformed</div></div>
  <div class="stat" style="left:722px"><div class="stat-ring"><span>11+</span></div><div class="stat-label">Year Followup</div></div>
  <div class="stat" style="left:1006px"><div class="stat-ring"><span>1K+</span></div><div class="stat-label">Qualified Specialists</div></div>
</section>

<!-- About -->
<section>
  <h2 class="sec-title" style="left:132px;top:1120px">About Us</h2>
  <div class="sec-sub" style="left:132px;top:1159px">WHO WE ARE <i></i></div>
  <p class="about-lead">Lorem ipsum dolor sit amet, consectetur adipiscing elit,</p>
  <p class="about-body">sed do eiusmod tempor incididunt ut labore et dolore magna aliqua. Ut enim ad minim veniam, quis nostrud exercitation ullamco laboris nisi ut aliquip ex ea commodo consequat. Duis aute irure dolor in reprehenderit in voluptate velit esse cillum dolore eu fugiat nulla pariatur. Excepteur sint occaecat cupidatat non proident, sunt in culpa qui officia deserunt mollit anim id est laborum</p>
  <span class="btn" style="left:132px;top:1468px;width:140px;height:44px;font-size:12px;font-weight:600">KNOW MORE</span>
  <div class="ring-photo" style="left:642px;top:1097px;width:440px;height:440px">
    <div class="photo" role="img" aria-label="Photo of a dentist examining a patient's teeth" style="left:12px;top:12px;width:410px;height:410px;background:linear-gradient(135deg,#dbe4ee,#a9c2dd 60%,#5f86c9)"></div>
  </div>
</section>

<!-- Services -->
<section>
  <h2 class="sec-title" style="left:0;top:1680px;width:1200px;text-align:center">Our Services</h2>
  <div class="sec-sub" style="left:518px;top:1718px">
    <i></i>WHAT WE DO<i></i>
  </div>

  <article class="card" style="left:72px;top:1785px"><div class="photo" role="img" aria-label="Photo of a cosmetic dentistry treatment" style="background:linear-gradient(135deg,#e6e9ee,#c9b8b8 60%,#e2c9c6)"></div><h3>COSMETIC DENTISTRY</h3><p>Lorem ipsum dolor sit amet, consectetur adipiscing elit, sed do eiusmod tempor incididunt ut labore et dolore magna</p><span class="btn">READ MORE</span></article>
  <article class="card" style="left:438px;top:1785px"><div class="photo" role="img" aria-label="Photo of a tooth shade guide held near a smile" style="background:linear-gradient(135deg,#d8c8bc,#efe7df 60%,#cbb9a8)"></div><h3>IMPLANTS</h3><p>Lorem ipsum dolor sit amet, consectetur adipiscing elit, sed do eiusmod tempor incididunt ut labore et dolore magna</p><span class="btn">READ MORE</span></article>
  <article class="card" style="left:804px;top:1785px"><div class="photo" role="img" aria-label="Photo of a smiling woman brushing her teeth" style="background:linear-gradient(135deg,#f1f1f1,#dcd6d0 60%,#c6bdb4)"></div><h3>DENTAL HYGIENE</h3><p>Lorem ipsum dolor sit amet, consectetur adipiscing elit, sed do eiusmod tempor incididunt ut labore et dolore magna</p><span class="btn">READ MORE</span></article>

  <article class="card" style="left:72px;top:2270px"><div class="photo" role="img" aria-label="Photo of an emergency dental treatment" style="background:linear-gradient(135deg,#c7ced6,#b3b8cf 60%,#9fb3cf)"></div><h3>EMERGENCY SERVICES</h3><p>Lorem ipsum dolor sit amet, consectetur adipiscing elit, sed do eiusmod tempor incididunt ut labore et dolore magna</p><span class="btn">READ MORE</span></article>
  <article class="card" style="left:438px;top:2270px"><div class="photo" role="img" aria-label="Photo of a dental restoration procedure" style="background:linear-gradient(135deg,#2f3d4e,#6f7f92 55%,#3b4a5c)"></div><h3>RESTORATIONS</h3><p>Lorem ipsum dolor sit amet, consectetur adipiscing elit, sed do eiusmod tempor incididunt ut labore et dolore magna</p><span class="btn">READ MORE</span></article>
  <article class="card" style="left:804px;top:2270px"><div class="photo" role="img" aria-label="Photo of a dentist holding a set of dentures" style="background:linear-gradient(135deg,#e9eef2,#f2f2f2 55%,#e3a9ad)"></div><h3>DENTURES</h3><p>Lorem ipsum dolor sit amet, consectetur adipiscing elit, sed do eiusmod tempor incididunt ut labore et dolore magna</p><span class="btn">READ MORE</span></article>
</section>

<!-- Scheduling banner -->
<section class="banner" role="img" aria-label="Faded photo of a modern dental treatment room">
  <h2>MODERN DENTISTRY &amp; HEALTHCARE<br>FOR A BETTER TOMORROW</h2>
  <p>Lorem ipsum dolor sit amet, consectetur adipiscing elit, sed do eiusmod tempor incididunt ut labore et dolore magna aliqua. Quis ipsum suspendisse</p>
  <span class="btn" style="left:512px;top:292px;width:176px;height:47px;font-size:14px">SCHEDULING NOW</span>
</section>

<!-- Testimonials -->
<section>
  <div class="abs" style="left:0;top:3330px;width:2px;height:650px;background:var(--teal)"></div>
  <h2 class="sec-title" style="left:0;top:3348px;width:1200px;text-align:center">Our Testimonials</h2>
  <div class="sec-sub" style="left:508px;top:3388px"><i></i>CLIENT REVIEWS<i></i></div>

  <div class="quote-card" style="left:118px;top:3528px">
    <h4>Awesome Support...</h4><span class="stars">★★★★<span style="color:#555">★</span></span>
    <p>"Lorem ipsum dolor sit amet, consectetur adipiscing elit, sed do eiusmod tempor incididunt ut labore et dolore magna aliqua. Quis ipsum suspendisse ultrices gravida. Risus commodo viverra maecenas accumsan lacus vel facilisis."</p>
  </div>
  <div class="quote-card" style="left:627px;top:3528px">
    <h4>Great Services....</h4><span class="stars">★★★★<span style="color:#555">★</span></span>
    <p>"Lorem ipsum dolor sit amet, consectetur adipiscing elit, sed do eiusmod tempor incididunt ut labore et dolore magna aliqua. Quis ipsum suspendisse ultrices gravida. Risus commodo viverra maecenas accumsan lacus vel facilisis."</p>
  </div>
  <svg class="abs" style="left:228px;top:3734px" width="44" height="24" viewBox="0 0 44 24" aria-hidden="true"><polygon points="0,0 44,0 22,22" fill="#fff"/><polyline points="0,1 22,22 44,1" fill="none" stroke="var(--line)" stroke-width="1.5"/></svg>
  <svg class="abs" style="left:737px;top:3734px" width="44" height="24" viewBox="0 0 44 24" aria-hidden="true"><polygon points="0,0 44,0 22,22" fill="#fff"/><polyline points="0,1 22,22 44,1" fill="none" stroke="var(--line)" stroke-width="1.5"/></svg>
  <svg class="abs" style="left:180px;top:3490px" width="66" height="50" viewBox="0 0 66 50" aria-hidden="true"><g fill="var(--brand)"><path d="M2 48V30C2 14 10 4 26 0l2 6C18 9 14 16 14 24h14v24z"/><path d="M36 48V30C36 14 44 4 60 0l2 6C52 9 48 16 48 24h14v24z"/></g></svg>
  <svg class="abs" style="left:689px;top:3490px" width="66" height="50" viewBox="0 0 66 50" aria-hidden="true"><g fill="var(--brand)"><path d="M2 48V30C2 14 10 4 26 0l2 6C18 9 14 16 14 24h14v24z"/><path d="M36 48V30C36 14 44 4 60 0l2 6C52 9 48 16 48 24h14v24z"/></g></svg>

  <div class="avatar" role="img" aria-label="Portrait photo of the reviewer" style="left:226px;top:3744px"></div>
  <div class="person" style="left:310px;top:3764px">MARCUS HALE<small>Lorem ipsum</small></div>
  <div class="avatar" role="img" aria-label="Portrait photo of the reviewer" style="left:735px;top:3744px"></div>
  <div class="person" style="left:819px;top:3764px">DANIEL PRICE<small>Lorem ipsum</small></div>

  <span class="dot" style="left:570px;background:#888;border-color:#888"></span>
  <span class="dot" style="left:586px"></span>
  <span class="dot" style="left:602px"></span>
  <span class="dot" style="left:618px"></span>
</section>

<!-- Contact -->
<section>
  <h2 class="sec-title" style="left:86px;top:4100px">Contact Us</h2>
  <div class="sec-sub" style="left:86px;top:4140px">GET IN TOUCH <i style="margin-left:14px"></i></div>
  <p class="abs" style="left:86px;top:4186px;font-size:13px;color:var(--ink)">For more information,Please fill out the following and we will be in touch shortly</p>
  <div class="field" style="left:86px;top:4232px;width:269px">First Name</div>
  <div class="field" style="left:380px;top:4232px;width:270px">Last Name</div>
  <div class="field" style="left:86px;top:4305px;width:269px">Phone</div>
  <div class="field" style="left:380px;top:4305px;width:270px">Company Name</div>
  <div class="field" style="left:86px;top:4375px;width:564px">Email</div>
  <span class="btn" style="left:86px;top:4455px;width:122px;height:42px;font-size:12px">SUBMIT</span>
  <div class="ring-photo" style="left:745px;top:4097px;width:430px;height:430px">
    <div class="photo" role="img" aria-label="Photo of a dentist in protective gear treating a smiling patient" style="left:10px;top:10px;width:404px;height:404px;background:linear-gradient(135deg,#dfe6ec,#eef2f5 45%,#c9b4a6)"></div>
  </div>
</section>

<!-- Footer -->
<footer class="footer">
  <div class="logo" style="left:64px;top:186px;width:208px;color:#fff">
    <span class="name" style="font-size:36px">Harrowfield</span>
    <span class="sub" style="font-size:14px;margin-top:5px">— DENTISTRY —</span>
  </div>

  <h3 class="f-head" style="left:346px;font-weight:400">LINKS</h3>
  <span class="f-item" style="left:368px;top:188px">About Us</span>
  <span class="f-item" style="left:368px;top:220px">Our Services</span>
  <span class="f-item" style="left:368px;top:252px">Testimonials</span>
  <span class="f-item" style="left:368px;top:284px">Contact us</span>

  <h3 class="f-head" style="left:542px;font-weight:400">CONTACT US</h3>
  <span class="f-icon" style="left:545px;top:196px"><svg width="16" height="16" viewBox="0 0 24 24" aria-hidden="true"><path d="M6 3c1-1 2-1 3 0l2 3c1 1 0 2.5-1 3 1.5 2.5 3 4 5 5 .5-1 2-2 3-1l3 2c1 1 1 2 0 3-3 3-7 2-11-2S3 6 6 3z" fill="#fff"/></svg></span>
  <span class="f-text" style="left:594px;top:202px">5550142876</span>
  <span class="f-icon" style="left:545px;top:249px"><svg width="16" height="16" viewBox="0 0 24 24" aria-hidden="true"><rect x="2" y="5" width="20" height="14" rx="2" fill="#fff"/><polyline points="3,6 12,13 21,6" fill="none" stroke="var(--teal)" stroke-width="2"/></svg></span>
  <span class="f-text" style="left:594px;top:255px">info@companyname.com</span>
  <span class="f-icon" style="left:545px;top:296px"><svg width="16" height="16" viewBox="0 0 24 24" aria-hidden="true"><path d="M12 2a7 7 0 0 1 7 7c0 5-7 13-7 13S5 14 5 9a7 7 0 0 1 7-7z" fill="#fff"/><circle cx="12" cy="9" r="2.5" fill="var(--teal)"/></svg></span>
  <span class="f-text" style="left:594px;top:290px">Lorem ipsum,Lorem ipsum,<br>Lorem ipsum.</span>

  <h3 class="f-head" style="left:876px;font-weight:400">Operating Hours</h3>
  <span class="f-item" style="left:898px;top:188px">Monday&nbsp;&nbsp; 8.30 AM - 5.00PM</span>
  <span class="f-item" style="left:898px;top:220px">Tuesday&nbsp;&nbsp; 8.30 AM - 5.00PM</span>
  <span class="f-item" style="left:898px;top:252px">Wednesday&nbsp;&nbsp; 8.30 AM - 5.00PM</span>
  <span class="f-item" style="left:898px;top:284px">Thursday&nbsp;&nbsp; 8.30 AM - 5.00PM</span>
  <span class="f-item" style="left:898px;top:316px">Friday&nbsp; 8.30 AM - 5.00PM</span>
  <span class="f-item" style="left:898px;top:348px">Saturday By Appointment Only</span>

  <p class="copyright" style="top:442px">Copyright © 2025 All Rights Reserved By Company Name</p>
</footer>
<span class="social" style="left:117px"></span>
<span class="social" style="left:157px"></span>
<span class="social" style="left:197px"></span>

</body>
</html>
```